Fun, Clean Business Card For Family Focused Travel Agency

I need a business card using specific colors and fonts as in the uploaded files. Ideally, I would like a large image of the logo on the back and all the contact info on the front. Maybe the stars/dots somewhere in a flowy form.

I do want it the contact information to be clear and easy to read. I don't want it to look too busy. Maybe even a bit minimalist.

I plan or ordering the ROUNDED CORNER business cards from Cardwell Press, so please consider that in your design.

Target Market(s)

Families with children, couples, groups of friends

Contact Information for Business Card

Marla Quint, Owner
Marla@TumbleTrips.example
Cell Phone Number 555-218-4603
Office Phone Number 555-647-1925
Specializing in Glimmerland destinations, Pelican Bay Fun Park, Cruises and All-Inclusive Vacations.

Nice but not required:
www.TumbleTrips.example
Facebook, Instagram, Twitter icons with username: TumbleTrips

Font styles to use
Sans Serif

Requirements
Must have
• Please try to use the colors from the logo as much as possible. I understand lighter shades/colors may be needed for some things.
Should not have
• NO SERIF FONTS. That is really the only thing I do not want at all

```html
<!DOCTYPE html>
<html lang="en">
<head>
<meta charset="utf-8">
<title>Tumble Trips – Business Card</title>
<link rel="stylesheet" href="https://fonts.googleapis.com/css2?family=Fira+Sans:wght@400;500;700&display=swap">
<style>
  :root {
    --teal: #1fb199;
    --teal-soft: #48c3ae;
    --navy: #151a33;
    --white: #ffffff;
    --backdrop: #6e6e6e;
    --backdrop-light: #8c8c8c;
  }
  html, body {
    margin: 0;
    width: 1200px;
    height: 900px;
    overflow: hidden;
  }
  body {
    background: radial-gradient(ellipse at 50% 40%, var(--backdrop-light), var(--backdrop));
    font-family: "Fira Sans", Arial, sans-serif;
    position: relative;
  }
  .card {
    position: absolute;
    width: 540px;
    height: 320px;
    border-radius: 24px;
    overflow: hidden;
    box-shadow: 0 18px 30px rgba(0,0,0,0.35);
  }

  /* ---------- Back card ---------- */
  .card-back {
    left: 600px;
    top: 110px;
    background: var(--teal);
    color: var(--white);
  }
  .card-back .brand {
    position: absolute;
    left: 0; right: 0; top: 78px;
    display: flex;
    align-items: center;
    justify-content: center;
    gap: 16px;
  }
  .brand-dot {
    flex: none;
    width: 56px; height: 56px;
    border-radius: 50%;
    background: var(--white);
  }
  .brand-name {
    font-size: 50px;
    font-weight: 700;
    letter-spacing: 0.5px;
    white-space: nowrap;
  }
  .card-back .brand-name { color: var(--white); }
  .specialties {
    position: absolute;
    left: 28px; right: 28px; bottom: 46px;
    text-align: center;
  }
  .specialties-title {
    font-size: 14px;
    font-weight: 700;
    color: var(--navy);
    margin-bottom: 8px;
  }
  .specialties-list {
    font-size: 11.5px;
    display: flex;
    justify-content: center;
    gap: 10px;
    white-space: nowrap;
  }
  .specialties-list span::before {
    content: "";
    display: inline-block;
    width: 4px; height: 4px;
    background: var(--white);
    transform: rotate(45deg);
    margin-right: 5px;
    vertical-align: middle;
  }

  /* ---------- Front card ---------- */
  .card-front {
    left: 60px;
    top: 500px;
    background: var(--white);
  }
  .card-front .panel {
    position: absolute;
    inset: 0;
  }
  .contact {
    position: absolute;
    left: 26px; top: 24px;
    color: var(--white);
  }
  .contact-name {
    font-size: 20px;
    font-weight: 700;
    color: var(--navy);
    margin: 0;
  }
  .contact-role {
    font-size: 16px;
    color: var(--navy);
    margin: 0 0 22px;
  }
  .contact-line {
    display: flex;
    align-items: center;
    gap: 10px;
    font-size: 13px;
    margin-bottom: 8px;
    white-space: nowrap;
  }
  .contact-line svg { width: 14px; height: 14px; fill: var(--navy); flex: none; }
  .website {
    position: absolute;
    left: 26px; top: 241px;
    font-size: 15px;
    color: var(--white);
    white-space: nowrap;
  }
  .card-front .brand {
    position: absolute;
    left: 300px; top: 122px;
    display: flex;
    align-items: center;
    gap: 10px;
  }
  .card-front .brand-dot { width: 38px; height: 38px; background: var(--teal); }
  .card-front .brand-name { font-size: 30px; color: var(--navy); }
  .social {
    position: absolute;
    left: 300px; top: 286px;
    display: flex;
    align-items: center;
    gap: 6px;
    color: var(--white);
    font-size: 16px;
  }
  .social-box {
    width: 13px; height: 13px;
    background: var(--navy);
    border-radius: 2px;
  }
  .social-handle { margin-left: 10px; }
</style>
</head>
<body>

  <section class="card card-back" aria-label="Card back">
    <div class="brand">
      <span class="brand-dot"></span>
      <span class="brand-name">Tumble Trips</span>
    </div>
    <div class="specialties">
      <div class="specialties-title">Specializing in</div>
      <div class="specialties-list">
        <span>Glimmerland destinations</span>
        <span>Pelican Bay Fun Park</span>
        <span>Cruises and All-Inclusive Vacations</span>
      </div>
    </div>
  </section>

  <section class="card card-front" aria-label="Card front">
    <svg class="panel" viewBox="0 0 540 320" preserveAspectRatio="none">
      <polygon points="0,0 290,0 240,230 0,230" fill="var(--teal)"/>
      <polygon points="290,0 308,0 258,230 240,230" fill="var(--navy)"/>
      <rect x="0" y="230" width="250" height="40" fill="var(--navy)"/>
      <rect x="0" y="270" width="540" height="50" fill="var(--teal)"/>
    </svg>

    <div class="contact">
      <p class="contact-name">Marla Quint</p>
      <p class="contact-role">Owner</p>
      <div class="contact-line">
        <svg viewBox="0 0 16 16"><rect x="4" y="1" width="8" height="14" rx="1.5"/><rect x="5.5" y="3" width="5" height="8" fill="var(--teal)"/></svg>
        <span>555-218-4603</span>
      </div>
      <div class="contact-line">
        <svg viewBox="0 0 16 16"><path d="M2 6 Q8 1 14 6 L12 8 L10 6.5 L6 6.5 L4 8 Z"/><rect x="3" y="9" width="10" height="5" rx="1"/></svg>
        <span>555-647-1925</span>
      </div>
      <div class="contact-line">
        <svg viewBox="0 0 16 16"><rect x="1" y="3" width="14" height="10" rx="1"/><path d="M1.5 3.5 L8 9 L14.5 3.5" fill="none" stroke="var(--teal)" stroke-width="1.4"/></svg>
        <span>Marla@TumbleTrips.example</span>
      </div>
    </div>

    <div class="website">www.TumbleTrips.example</div>

    <div class="brand">
      <span class="brand-dot"></span>
      <span class="brand-name">Tumble Trips</span>
    </div>

    <div class="social">
      <span class="social-box"></span>
      <span class="social-box"></span>
      <span class="social-box"></span>
      <span class="social-handle">TumbleTrips</span>
    </div>
  </section>

</body>
</html>
```